Agrarhandel benötigt Homepage
Zielgruppe
Wir sind ein Agrarhandel mit einem Warenumschlagslager im Sinne eines klassischen Einzelhandels und vertreiben Produkte an Landwirte.
Wir vertreiben folgende Hauptproduktgruppen:
Einzelfuttermittel
wie z.B. Sojaexktraktionsschrot. Die einzelnen Produkte könnten z.B. wie die Futtermittel auf folgender Seite dargestellt werden (https://www.kornprobe-beispiel.eu/de/produkt/trelomixan)
Mischfuttermittel
Hier bieten wir unseren Kunden an, individuelles Mischfutter auf Basis unserer Einzelfuttermittel herzustellen.
Weitere Details und weitere Produktbereiche habe ich in einer Powerpoint-Übersicht dargestellt.
Neben diesen Produkten wollen wir uns als Familienunternehmen selbst vorstellen. Zudem betreiben wir in unserer Familie zusätzlich einen Milchviehbetrieb den wir ebenfalls hervorheben möchten, da wir unseren Kunden gegenüber einerseits als Zulieferer aber auch als Kollege auftreten wollen.
Einzelfuttermittel: Hier können wir durch unsere Unabhängigkeit punkten, da wir nicht abhängig von bestimmten Lieferanten sind und dementsprechend unabhängig beraten können. Wir untersuchen im Vergleich zu unseren Wettbewerben die Qualität der Futtermittel bis ins Detail und können daher eine Transparenz bieten, die Konkurrenten in der Regel nicht bieten können. Unser Warenumschlagsplatz mit moderner Technik ermöglicht es uns äußerst kosteneffizient die Waren umschlagen und ausliefern zu können.
Mischfuttermittel: Auf Basis der vorhandenen Einzelfuttermittel stellen wir je nach Kundenwunsch individuelle Mischfutter her. Wir arbeiten mit offenen Deklarationen, sodass unsere Kunden jederzeit nachvollziehen können, ob auch die Einzelfuttermittel verwendet wurden, die sie bestellt haben und keine billigen Ersatzprodukte verwendet wurden.
Zudem sind wir BT und HUPA zertifiziert. Die aktuellen für unser Unternehmen ausgestellten Zertifikate müssen für unsere Kunden als Download zur Verfügung stehen. Statt dem HUPA-Logo bitte das ..
Aufgabenstellung
Wir möchten gerne ein zeitgemäße Homepage, jedoch muss auch berücksichtigt werden, dass unsere Kunden eher konservativ denken.

```html
<!DOCTYPE html>
<html lang="de">
<head>
<meta charset="utf-8">
<title>Brandtner Agrarhandel – Seitenentwürfe</title>
<link href="https://fonts.googleapis.com/css2?family=Poppins:wght@400;500;600;700;800&family=Inter:wght@400;500;600;700&display=swap" rel="stylesheet">
<style>
:root{
  --ink:#1e1e1f;
  --dark:#262627;
  --yellow:#f5c823;
  --amber:#f2a81d;
  --orange:#f29a12;
  --rule:#cfcfcf;
  --field:#d9d9d9;
  --white:#ffffff;
  --muted:#bdbdbd;
  --wheat-a:#c98a2e;
  --wheat-b:#8a5a1e;
  --green-a:#6f7a3a;
  --sky:#d9b66a;
}
*{box-sizing:border-box;margin:0;padding:0}
html,body{width:1200px;height:1200px;overflow:hidden;background:var(--white)}
body{font-family:"Inter",sans-serif;color:var(--ink);position:relative}
.stage{position:absolute;left:0;top:0;width:1932px;height:1932px;transform:scale(.621118);transform-origin:0 0;overflow:hidden}
.page{position:absolute;width:884px;transform-origin:0 0}
.page *{position:absolute}
.page svg *{position:static}

/* header */
.site-header{left:0;top:0;width:884px;height:92px}
.brand-tab{left:0;top:0;width:50px;height:84px;background:var(--amber)}
.nav-bar{left:62px;top:0;width:822px;height:84px;background:var(--ink)}
.nav-rule{left:50px;top:84px;width:834px;height:7px;background:var(--rule)}
.brand{font-family:"Poppins",sans-serif;font-weight:700;font-size:25px;color:var(--yellow);white-space:nowrap}
.nav-bar .brand{left:24px;top:24px}
.nav{left:322px;top:39px;display:flex;gap:11px;font-family:"Poppins",sans-serif;font-weight:700;font-size:9.5px;color:var(--white);letter-spacing:.2px}
.nav span{position:static}
.nav .active{color:var(--orange)}
.search{left:780px;top:34px;width:20px;height:20px}

/* image areas */
.photo{border-radius:0}
.ph-field{background:linear-gradient(180deg,#b08a4a 0%,#c99a4e 22%,#7d7a35 45%,#5e5a2c 75%,#6a4e2a 100%)}
.ph-wheat{background:linear-gradient(160deg,#e4b46a 0%,#c98a2e 45%,#8a5a1e 100%)}
.ph-hands{background:linear-gradient(150deg,#b96a5a 0%,#d6a25e 45%,#a36a2a 100%)}
.ph-bales{background:linear-gradient(180deg,#a9b4c0 0%,#d7b06a 35%,#b07a32 100%)}
.ph-harvest{background:linear-gradient(165deg,#f0b35a 0%,#b8742a 50%,#5e3a1a 100%)}
.ph-green{background:linear-gradient(170deg,#f2e6a8 0%,#9aa64a 45%,#4f6328 100%)}
.ph-seeds{background:linear-gradient(140deg,#5c5a44 0%,#8c8668 40%,#e8e4da 55%,#6a4a34 100%)}
.ph-avatar{background:#e9e9e9;border-radius:50%;border:3px solid var(--white);box-shadow:0 2px 6px rgba(0,0,0,.25)}

/* home */
.hero-kicker{left:0;width:884px;text-align:center;font-family:"Poppins",sans-serif;font-weight:600;font-size:12px;color:#6b5a3a;letter-spacing:1px}
.hero-title{left:0;width:884px;text-align:center;font-family:"Poppins",sans-serif;font-weight:800;font-size:25px;color:var(--yellow);letter-spacing:.3px}
.hero-sub{left:292px;width:300px;text-align:center;font-family:"Poppins",sans-serif;font-weight:700;font-size:9.5px;line-height:13px;color:var(--white)}
.pill{background:var(--yellow);border-radius:12px}
.pill-label{display:flex;align-items:center;justify-content:center;font-family:"Poppins",sans-serif;font-weight:700;font-size:11px;color:#3a2c00}
.intro-lead{font-family:"Poppins",sans-serif;font-weight:700;font-size:17px;line-height:21px;color:var(--ink)}
.callout-text{font-family:"Inter",sans-serif;font-size:9px;line-height:11.5px;color:var(--white)}

.why{left:0;width:884px;height:342px}
.why-title{left:213px;top:38px;font-family:"Inter",sans-serif;font-weight:500;font-size:21px;color:var(--white)}
.why-sub{left:213px;top:78px;width:290px;font-size:7.5px;line-height:10px;color:#cfcfcf}
.why-item{width:120px}
.why-dot{left:0;top:0;width:14px;height:14px;border-radius:50%;background:var(--yellow)}
.why-item b{position:absolute;left:22px;top:0;font-size:7.5px;color:var(--white);font-weight:700}
.why-item p{position:absolute;left:22px;top:11px;width:92px;font-size:7px;line-height:9px;color:#cfcfcf}

.section-title{font-family:"Inter",sans-serif;font-weight:600;color:var(--ink);text-align:center}
.quote-text{font-size:9px;line-height:12px;color:var(--white)}
.dot-bar{height:6px;border-radius:3px}

/* footer */
.site-footer{left:0;width:884px;height:275px}
.foot-dark{left:0;top:0;width:884px;height:245px;background:var(--dark)}
.foot-band{left:0;top:245px;width:884px;height:30px;background:var(--yellow)}
.foot-line{top:43px;width:2px;height:110px;background:var(--muted)}
.foot-line::before,.foot-line::after{content:"";position:absolute;left:-3px;width:8px;height:8px;border-radius:50%;background:var(--muted)}
.foot-line::before{top:-2px}.foot-line::after{bottom:-2px}
.foot-title{left:290px;top:48px;font-size:15px;font-weight:500;color:var(--white)}
.field{height:16px;background:var(--field);font-size:7px;color:#555;padding:3px 6px}
.send{left:499px;top:115px;width:94px;height:16px;background:var(--yellow);border-radius:4px;font-size:8px;font-weight:700;color:#3a2c00;text-align:center;line-height:16px}
.info{left:650px;font-size:7.5px;color:#cfcfcf;white-space:nowrap}
.info i{position:absolute;left:-11px;top:1px;width:7px;height:7px;background:#cfcfcf;border-radius:50%}
.footer-brand{left:0;width:884px;top:155px;text-align:center}
.footer-brand .brand{position:static}
.social{top:215px;width:14px;height:14px;background:var(--white);border-radius:3px}
.copyright{left:0;top:253px;width:884px;text-align:center;font-size:8px;font-weight:700;color:#3a2c00}

/* partners */
.partner-label{left:131px;width:622px;text-align:center;font-family:"Poppins",sans-serif;font-weight:700;font-size:22px;color:#fff3d0}
.partner-badge{width:80px;height:80px;border-radius:50%;background:#f4a90f}

/* suppliers */
.sup-head{left:180px;font-family:"Poppins",sans-serif;font-weight:700;font-size:20px;color:var(--orange)}
.sup-text{left:183px;width:540px;font-size:13px;line-height:16px;color:var(--ink)}

/* products */
.prod-title{left:0;width:884px;text-align:center;font-family:"Inter",sans-serif;font-weight:600;font-size:21px;color:var(--ink)}
.tile{width:168px;height:168px;box-shadow:0 2px 6px rgba(0,0,0,.25)}
.col-title{width:200px;text-align:center;font-family:"Inter",sans-serif;font-weight:700;font-size:14px;color:var(--ink)}
.col-text{width:190px;text-align:center;font-size:12px;line-height:15px;color:var(--ink)}
</style>
</head>
<body>
<div class="stage">

<!-- ============ Startseite (groß) ============ -->
<section class="page page-home" style="left:0;top:152px;height:1538px;">
  <header class="site-header">
    <span class="brand-tab"></span>
    <div class="nav-bar">
      <span class="brand">Brandtner</span>
      <div class="nav"><span class="active">LANDWIRT</span><span>GESCHÄFTSPARTNER</span><span>LIEFERANTEN</span><span>PRODUKTE</span><span>FIRMENPRÄSENTATION</span></div>
      <svg class="search" viewBox="0 0 20 20"><circle cx="8" cy="8" r="6" fill="none" stroke="#fff" stroke-width="2"/><line x1="12.5" y1="12.5" x2="18" y2="18" stroke="#fff" stroke-width="2.5"/></svg>
    </div>
    <span class="nav-rule"></span>
  </header>

  <div class="photo ph-field" role="img" aria-label="Getreidefeld im Abendlicht" style="left:0;top:100px;width:884px;height:253px;"></div>
  <div class="hero-kicker" style="top:138px;">LOREM IPSUM</div>
  <div class="hero-title" style="top:155px;">CONSECTETUR ADIPISCING ELIT</div>
  <div class="hero-sub" style="top:194px;">Excepteur sint occaecat cupidatat non proident, sunt in culpa qui officia deserunt mollit anim id es</div>
  <div class="pill" style="left:408px;top:230px;width:67px;height:16px;"></div>

  <div class="photo ph-hands" role="img" aria-label="Hände halten Weizenähren" style="left:216px;top:298px;width:144px;height:98px;"></div>
  <div class="photo ph-bales" role="img" aria-label="Strohballen auf dem Feld" style="left:370px;top:298px;width:144px;height:98px;"></div>
  <div class="photo ph-wheat" role="img" aria-label="Weizenähren in Nahaufnahme" style="left:524px;top:298px;width:144px;height:98px;"></div>

  <div class="intro-lead" style="left:215px;top:443px;width:190px;">Excepteur sint occaecat cupidatat non proident, sunt in culpa</div>
  <svg style="left:422px;top:425px;width:246px;height:121px;" viewBox="0 0 246 121"><polygon points="30,0 246,0 246,121 30,121 0,61" fill="#f5c823"/></svg>
  <div class="callout-text" style="left:456px;top:448px;width:200px;">Sed ut perspiciatis unde omnis iste natus error sit voluptatem accusantium doloremque laudantium, to<br>Sed ut perspiciatis unde omnis iste natus error sit voluptatem accusantium doloremque laudantium, to</div>

  <div class="why" style="top:596px;">
    <svg style="left:0;top:0;width:884px;height:342px;" viewBox="0 0 884 342"><polygon points="0,0 884,0 884,342 0,222" fill="#262627"/></svg>
    <div class="why-title">Warum Uns Wählen?</div>
    <div class="why-sub">Excepteur sint occaecat cupidatat non proident, sunt in culpa qui officia deserunt mollit anim id es</div>
    <div class="why-item" style="left:211px;top:114px;"><span class="why-dot"></span><b>Lorem Ipsum</b><p>Excepteur sint occaecat cupidatat non proident, sunt in culpa</p></div>
    <div class="why-item" style="left:347px;top:114px;"><span class="why-dot"></span><b>Lorem Ipsum</b><p>Excepteur sint occaecat cupidatat non proident, sunt in culpa</p></div>
    <div class="why-item" style="left:211px;top:169px;"><span class="why-dot"></span><b>Lorem Ipsum</b><p>Excepteur sint occaecat cupidatat non proident, sunt in culpa</p></div>
    <div class="why-item" style="left:347px;top:169px;"><span class="why-dot"></span><b>Lorem Ipsum</b><p>Excepteur sint occaecat cupidatat non proident, sunt in culpa</p></div>
    <div class="pill" style="left:387px;top:235px;width:68px;height:17px;"></div>
    <div style="left:545px;top:39px;width:300px;height:205px;background:var(--yellow);border-radius:4px;"></div>
    <div class="photo ph-harvest" role="img" aria-label="Mähdrescher bei der Weizenernte" style="left:535px;top:49px;width:300px;height:205px;"></div>
  </div>

  <div class="section-title" style="left:0;top:946px;width:884px;font-size:19px;">Die Leute Sagen Über Uns</div>
  <svg style="left:0;top:1020px;width:884px;height:134px;" viewBox="0 0 884 134">
    <path d="M0,6 L106,6 Q126,6 126,26 L126,114 Q126,134 106,134 L0,134 Z" fill="#f5c823"/>
    <path d="M238,43 L642,0 Q665,0 665,22 L665,111 Q665,133 642,133 L238,133 Q215,133 215,111 L215,66 Q215,45 238,43 Z" fill="#f5c823"/>
    <path d="M770,40 L884,11 L884,134 L770,134 Q748,134 748,112 L748,62 Q748,45 770,40 Z" fill="#f5c823"/>
  </svg>
  <div class="photo ph-avatar" role="img" aria-label="Porträt eines Kunden" style="left:37px;top:985px;width:66px;height:66px;"></div>
  <div class="photo ph-avatar" role="img" aria-label="Porträt einer Kundin" style="left:584px;top:985px;width:66px;height:66px;"></div>
  <div class="quote-text" style="left:265px;top:1080px;width:360px;">Sed ut perspiciatis unde omnis iste natus error sit voluptatem accusantium doloremque laudantium, to<br>Sed ut perspiciatis unde omnis iste natus error sit voluptatem accusantium doloremque laudantium, to</div>
  <div class="dot-bar" style="left:360px;top:1191px;width:45px;background:var(--ink);"></div>
  <div class="dot-bar" style="left:419px;top:1191px;width:45px;background:var(--yellow);"></div>
  <div class="dot-bar" style="left:479px;top:1191px;width:45px;background:var(--yellow);"></div>

  <footer class="site-footer" style="top:1263px;">
    <div class="foot-dark"></div><div class="foot-band"></div>
    <span class="foot-line" style="left:262px;"></span><span class="foot-line" style="left:620px;"></span>
    <div class="foot-title">Kontak Uns</div>
    <div class="field" style="left:291px;top:77px;width:93px;">Name</div>
    <div class="field" style="left:398px;top:77px;width:90px;">Email</div>
    <div class="field" style="left:499px;top:77px;width:94px;">Telefonnummer</div>
    <div class="field" style="left:291px;top:107px;width:197px;height:23px;">Nachricht</div>
    <div class="send">Schicken</div>
    <div class="info" style="top:83px;"><i></i>Location</div>
    <div class="info" style="top:97px;"><i></i>+49 5431 908765</div>
    <div class="info" style="top:111px;"><i></i>kontakt@brandtner-agrar.de</div>
    <div class="footer-brand"><span class="brand">Brandtner</span></div>
    <span class="social" style="left:408px;"></span><span class="social" style="left:426px;"></span><span class="social" style="left:444px;"></span><span class="social" style="left:462px;"></span>
    <div class="copyright">Copyright 2023 All Right Reserved</div>
  </footer>
</section>

<!-- ============ Startseite (klein) ============ -->
<section class="page page-home-small" style="left:910px;top:6px;height:1538px;transform:scale(.4276);">
  <header class="site-header">
    <span class="brand-tab"></span>
    <div class="nav-bar">
      <span class="brand">Brandtner</span>
      <div class="nav"><span class="active">LANDWIRT</span><span>GESCHÄFTSPARTNER</span><span>LIEFERANTEN</span><span>PRODUKTE</span><span>FIRMENPRÄSENTATION</span></div>
      <svg class="search" viewBox="0 0 20 20"><circle cx="8" cy="8" r="6" fill="none" stroke="#fff" stroke-width="2"/><line x1="12.5" y1="12.5" x2="18" y2="18" stroke="#fff" stroke-width="2.5"/></svg>
    </div>
    <span class="nav-rule"></span>
  </header>
  <div class="photo ph-field" role="img" aria-label="Getreidefeld im Abendlicht" style="left:0;top:100px;width:884px;height:253px;"></div>
  <div class="hero-kicker" style="top:138px;">LOREM IPSUM</div>
  <div class="hero-title" style="top:155px;">CONSECTETUR ADIPISCING ELIT</div>
  <div class="hero-sub" style="top:194px;">Excepteur sint occaecat cupidatat non proident, sunt in culpa qui officia deserunt mollit anim id es</div>
  <div class="pill" style="left:408px;top:230px;width:67px;height:16px;"></div>
  <div class="photo ph-hands" role="img" aria-label="Hände halten Weizenähren" style="left:216px;top:298px;width:144px;height:98px;"></div>
  <div class="photo ph-bales" role="img" aria-label="Strohballen auf dem Feld" style="left:370px;top:298px;width:144px;height:98px;"></div>
  <div class="photo ph-wheat" role="img" aria-label="Weizenähren in Nahaufnahme" style="left:524px;top:298px;width:144px;height:98px;"></div>
  <div class="intro-lead" style="left:215px;top:443px;width:190px;">Excepteur sint occaecat cupidatat non proident, sunt in culpa</div>
  <svg style="left:422px;top:425px;width:246px;height:121px;" viewBox="0 0 246 121"><polygon points="30,0 246,0 246,121 30,121 0,61" fill="#f5c823"/></svg>
  <div class="callout-text" style="left:456px;top:448px;width:200px;">Sed ut perspiciatis unde omnis iste natus error sit voluptatem accusantium doloremque laudantium, to<br>Sed ut perspiciatis unde omnis iste natus error sit voluptatem accusantium doloremque laudantium, to</div>
  <div class="why" style="top:596px;">
    <svg style="left:0;top:0;width:884px;height:342px;" viewBox="0 0 884 342"><polygon points="0,0 884,0 884,342 0,222" fill="#262627"/></svg>
    <div class="why-title">Warum Uns Wählen?</div>
    <div class="why-sub">Excepteur sint occaecat cupidatat non proident, sunt in culpa qui officia deserunt mollit anim id es</div>
    <div class="why-item" style="left:211px;top:114px;"><span class="why-dot"></span><b>Lorem Ipsum</b><p>Excepteur sint occaecat cupidatat non proident, sunt in culpa</p></div>
    <div class="why-item" style="left:347px;top:114px;"><span class="why-dot"></span><b>Lorem Ipsum</b><p>Excepteur sint occaecat cupidatat non proident, sunt in culpa</p></div>
    <div class="why-item" style="left:211px;top:169px;"><span class="why-dot"></span><b>Lorem Ipsum</b><p>Excepteur sint occaecat cupidatat non proident, sunt in culpa</p></div>
    <div class="why-item" style="left:347px;top:169px;"><span class="why-dot"></span><b>Lorem Ipsum</b><p>Excepteur sint occaecat cupidatat non proident, sunt in culpa</p></div>
    <div class="pill" style="left:387px;top:235px;width:68px;height:17px;"></div>
    <div style="left:545px;top:39px;width:300px;height:205px;background:var(--yellow);border-radius:4px;"></div>
    <div class="photo ph-harvest" role="img" aria-label="Mähdrescher bei der Weizenernte" style="left:535px;top:49px;width:300px;height:205px;"></div>
  </div>
  <div class="section-title" style="left:0;top:946px;width:884px;font-size:19px;">Die Leute Sagen Über Uns</div>
  <svg style="left:0;top:1020px;width:884px;height:134px;" viewBox="0 0 884 134">
    <path d="M0,6 L106,6 Q126,6 126,26 L126,114 Q126,134 106,134 L0,134 Z" fill="#f5c823"/>
    <path d="M238,43 L642,0 Q665,0 665,22 L665,111 Q665,133 642,133 L238,133 Q215,133 215,111 L215,66 Q215,45 238,43 Z" fill="#f5c823"/>
    <path d="M770,40 L884,11 L884,134 L770,134 Q748,134 748,112 L748,62 Q748,45 770,40 Z" fill="#f5c823"/>
  </svg>
  <div class="photo ph-avatar" role="img" aria-label="Porträt eines Kunden" style="left:37px;top:985px;width:66px;height:66px;"></div>
  <div class="photo ph-avatar" role="img" aria-label="Porträt einer Kundin" style="left:584px;top:985px;width:66px;height:66px;"></div>
  <div class="quote-text" style="left:265px;top:1080px;width:360px;">Sed ut perspiciatis unde omnis iste natus error sit voluptatem accusantium doloremque laudantium, to<br>Sed ut perspiciatis unde omnis iste natus error sit voluptatem accusantium doloremque laudantium, to</div>
  <div class="dot-bar" style="left:360px;top:1191px;width:45px;background:var(--ink);"></div>
  <div class="dot-bar" style="left:419px;top:1191px;width:45px;background:var(--yellow);"></div>
  <div class="dot-bar" style="left:479px;top:1191px;width:45px;background:var(--yellow);"></div>
  <footer class="site-footer" style="top:1263px;">
    <div class="foot-dark"></div><div class="foot-band"></div>
    <span class="foot-line" style="left:262px;"></span><span class="foot-line" style="left:620px;"></span>
    <div class="foot-title">Kontak Uns</div>
    <div class="field" style="left:291px;top:77px;width:93px;">Name</div>
    <div class="field" style="left:398px;top:77px;width:90px;">Email</div>
    <div class="field" style="left:499px;top:77px;width:94px;">Telefonnummer</div>
    <div class="field" style="left:291px;top:107px;width:197px;height:23px;">Nachricht</div>
    <div class="send">Schicken</div>
    <div class="info" style="top:83px;"><i></i>Location</div>
    <div class="info" style="top:97px;"><i></i>+49 5431 908765</div>
    <div class="info" style="top:111px;"><i></i>kontakt@brandtner-agrar.de</div>
    <div class="footer-brand"><span class="brand">Brandtner</span></div>
    <span class="social" style="left:408px;"></span><span class="social" style="left:426px;"></span><span class="social" style="left:444px;"></span><span class="social" style="left:462px;"></span>
    <div class="copyright">Copyright 2023 All Right Reserved</div>
  </footer>
</section>

<!-- ============ Geschäftspartner ============ -->
<section class="page page-partners" style="left:910px;top:677px;height:1540px;transform:scale(.4276);">
  <header class="site-header">
    <span class="brand-tab"></span>
    <div class="nav-bar">
      <span class="brand">Brandtner</span>
      <div class="nav"><span class="active">LANDWIRT</span><span>GESCHÄFTSPARTNER</span><span>LIEFERANTEN</span><span>PRODUKTE</span><span>FIRMENPRÄSENTATION</span></div>
      <svg class="search" viewBox="0 0 20 20"><circle cx="8" cy="8" r="6" fill="none" stroke="#fff" stroke-width="2"/><line x1="12.5" y1="12.5" x2="18" y2="18" stroke="#fff" stroke-width="2.5"/></svg>
    </div>
    <span class="nav-rule"></span>
  </header>
  <div class="photo ph-harvest" role="img" aria-label="Unscharfer Mähdrescher im Weizenfeld" style="left:70px;top:175px;width:751px;height:966px;border:6px solid var(--yellow);box-shadow:0 8px 30px rgba(0,0,0,.35);"></div>
  <div style="left:131px;top:229px;width:622px;height:854px;background:rgba(255,235,200,.18);border:2px solid rgba(255,255,255,.35);border-radius:28px;"></div>
  <div class="partner-label" style="top:295px;">Geschäftspartner</div>
  <span class="partner-badge" style="left:194px;top:368px;"></span><span class="partner-badge" style="left:332px;top:368px;"></span><span class="partner-badge" style="left:470px;top:368px;"></span><span class="partner-badge" style="left:610px;top:368px;"></span>
  <div class="partner-label" style="top:546px;">Saatgutpartner</div>
  <span class="partner-badge" style="left:264px;top:626px;"></span><span class="partner-badge" style="left:402px;top:626px;"></span><span class="partner-badge" style="left:540px;top:626px;"></span>
  <div class="partner-label" style="top:818px;">Equipment partners</div>
  <span class="partner-badge" style="left:194px;top:892px;"></span><span class="partner-badge" style="left:332px;top:892px;"></span><span class="partner-badge" style="left:470px;top:892px;"></span><span class="partner-badge" style="left:610px;top:892px;"></span>
  <footer class="site-footer" style="top:1265px;">
    <div class="foot-dark"></div><div class="foot-band"></div>
    <span class="foot-line" style="left:262px;"></span><span class="foot-line" style="left:620px;"></span>
    <div class="foot-title">Kontak Uns</div>
    <div class="field" style="left:291px;top:77px;width:93px;">Name</div>
    <div class="field" style="left:398px;top:77px;width:90px;">Email</div>
    <div class="field" style="left:499px;top:77px;width:94px;">Telefonnummer</div>
    <div class="field" style="left:291px;top:107px;width:197px;height:23px;">Nachricht</div>
    <div class="send">Schicken</div>
    <div class="info" style="top:83px;"><i></i>Location</div>
    <div class="info" style="top:97px;"><i></i>+49 5431 908765</div>
    <div class="info" style="top:111px;"><i></i>kontakt@brandtner-agrar.de</div>
    <div class="footer-brand"><span class="brand">Brandtner</span></div>
    <span class="social" style="left:408px;"></span><span class="social" style="left:426px;"></span><span class="social" style="left:444px;"></span><span class="social" style="left:462px;"></span>
    <div class="copyright">Copyright 2023 All Right Reserved</div>
  </footer>
</section>

<!-- ============ Lieferanten ============ -->
<section class="page page-suppliers" style="left:910px;top:1350px;height:1360px;transform:scale(.4276);">
  <header class="site-header">
    <span class="brand-tab"></span>
    <div class="nav-bar">
      <span class="brand">Brandtner</span>
      <div class="nav"><span class="active">LANDWIRT</span><span>GESCHÄFTSPARTNER</span><span>LIEFERANTEN</span><span>PRODUKTE</span><span>FIRMENPRÄSENTATION</span></div>
      <svg class="search" viewBox="0 0 20 20"><circle cx="8" cy="8" r="6" fill="none" stroke="#fff" stroke-width="2"/><line x1="12.5" y1="12.5" x2="18" y2="18" stroke="#fff" stroke-width="2.5"/></svg>
    </div>
    <span class="nav-rule"></span>
  </header>
  <div class="photo ph-bales" role="img" aria-label="Runde Strohballen auf einem Feld" style="left:0;top:105px;width:884px;height:257px;"></div>
  <div style="left:365px;top:198px;width:154px;height:50px;background:rgba(210,160,110,.75);border-radius:10px;"></div>
  <div style="left:365px;top:207px;width:154px;text-align:center;font-family:'Poppins',sans-serif;font-weight:600;font-size:21px;color:#3a2a1a;">Lieferanten</div>
  <div class="photo ph-green" role="img" aria-label="Feld bei Sonnenaufgang" style="left:183px;top:304px;width:164px;height:112px;"></div>
  <div class="photo ph-field" role="img" aria-label="Ackerreihen im Abendlicht" style="left:358px;top:304px;width:164px;height:112px;"></div>
  <div class="photo ph-harvest" role="img" aria-label="Mähdrescher bei der Ernte" style="left:534px;top:304px;width:164px;height:112px;"></div>

  <div class="sup-head" style="top:470px;">Lorem ipsum dolor sit amet</div>
  <div class="sup-text" style="top:508px;font-weight:600;">Ut enim ad minim veniam, quis nostrud exercitation ullamco laboris nisi ut aliquip ex ea Ut enim ad minim veniam, quis nostrud exercitation ullamco laboris nisi ut aliquip ex ea commodo coUt enim ad minim veniam, quis nostrud exercitation ullamco laboris nisi ut aliquip ex ea commodo co con.</div>
  <div class="sup-head" style="top:641px;left:188px;">Duis aute irure dolor in reprehenderit</div>
  <div class="sup-text" style="top:680px;font-weight:600;">Ut enim ad minim veniam, quis nostrud exercitation ullamco laboris nisi ut aliquip ex ea Ut enim ad minim veniam, quis nostrud exercitation ullamco laboris nisi ut aliquip ex ea commodo coUt enim ad minim veniam, quis nostrud exercitation ullamco laboris nisi ut aliquip ex ea commodo co con.</div>
  <div class="sup-head" style="top:825px;left:193px;">Nemo enim ipsam voluptatem quia</div>
  <div class="sup-text" style="top:870px;width:570px;font-weight:600;">Lorem ipsum dolor sit amet, consectetur adipiscing elit, sed do eiusmod tempor incididunt ut labore Lorem ipsum dolor sit amet, consectetur adipiscing elit, sed do eiusmod tempor incididunt ut labore Lorem ipsum dolor sit amet, consectetur adipiscing elit, sed do eiusmod tempor incididunt ut labore</div>

  <footer class="site-footer" style="top:1076px;">
    <div class="foot-dark"></div><div class="foot-band"></div>
    <span class="foot-line" style="left:262px;"></span><span class="foot-line" style="left:620px;"></span>
    <div class="foot-title">Kontak Uns</div>
    <div class="field" style="left:291px;top:77px;width:93px;">Name</div>
    <div class="field" style="left:398px;top:77px;width:90px;">Email</div>
    <div class="field" style="left:499px;top:77px;width:94px;">Telefonnummer</div>
    <div class="field" style="left:291px;top:107px;width:197px;height:23px;">Nachricht</div>
    <div class="send">Schicken</div>
    <div class="info" style="top:83px;"><i></i>Location</div>
    <div class="info" style="top:97px;"><i></i>+49 5431 908765</div>
    <div class="info" style="top:111px;"><i></i>kontakt@brandtner-agrar.de</div>
    <div class="footer-brand"><span class="brand">Brandtner</span></div>
    <span class="social" style="left:408px;"></span><span class="social" style="left:426px;"></span><span class="social" style="left:444px;"></span><span class="social" style="left:462px;"></span>
    <div class="copyright">Copyright 2023 All Right Reserved</div>
  </footer>
</section>

<!-- ============ Produkte ============ -->
<section class="page page-products" style="left:1328px;top:0;height:1541px;transform:scale(.6833);">
  <header class="site-header">
    <span class="brand-tab"></span>
    <div class="nav-bar">
      <span class="brand">Brandtner</span>
      <div class="nav"><span class="active">LANDWIRT</span><span>GESCHÄFTSPARTNER</span><span>LIEFERANTEN</span><span>PRODUKTE</span><span>FIRMENPRÄSENTATION</span></div>
      <svg class="search" viewBox="0 0 20 20"><circle cx="8" cy="8" r="6" fill="none" stroke="#fff" stroke-width="2"/><line x1="12.5" y1="12.5" x2="18" y2="18" stroke="#fff" stroke-width="2.5"/></svg>
    </div>
    <span class="nav-rule"></span>
  </header>
  <div class="prod-title" style="top:164px;">Produkte</div>

  <div class="tile ph-seeds" role="img" aria-label="Säcke mit Saatgut und Körnern" style="left:168px;top:262px;"></div>
  <div class="tile ph-bales" role="img" aria-label="Strohballen" style="left:357px;top:262px;"></div>
  <div class="tile ph-hands" role="img" aria-label="Hände mit Weizenähren" style="left:546px;top:262px;"></div>
  <div class="tile ph-hands" role="img" aria-label="Hände mit Weizenähren" style="left:168px;top:448px;"></div>
  <div class="tile ph-wheat" role="img" aria-label="Weizenähren" style="left:357px;top:448px;"></div>
  <div class="tile ph-green" role="img" aria-label="Grünes Getreide im Gegenlicht" style="left:546px;top:448px;"></div>
  <div class="tile ph-bales" role="img" aria-label="Strohballen" style="left:168px;top:634px;"></div>
  <div class="tile ph-green" role="img" aria-label="Grünes Getreide im Gegenlicht" style="left:357px;top:634px;"></div>
  <div class="tile ph-seeds" role="img" aria-label="Säcke mit Saatgut und Körnern" style="left:546px;top:634px;"></div>

  <svg style="left:82px;top:516px;width:44px;height:38px;" viewBox="0 0 44 38"><polygon points="44,0 44,38 0,19" fill="#f2a81d"/></svg>
  <svg style="left:758px;top:516px;width:44px;height:38px;" viewBox="0 0 44 38"><polygon points="0,0 0,38 44,19" fill="#f2a81d"/></svg>

  <div class="pill pill-label" style="left:384px;top:840px;width:114px;height:31px;border-radius:9px;font-size:14px;">Mehr sehen</div>

  <svg style="left:0;top:911px;width:884px;height:342px;" viewBox="0 0 884 342"><polygon points="0,0 884,0 884,341 0,224" fill="#f5c823"/></svg>
  <div class="col-title" style="left:136px;top:966px;">Lorem Ipsum</div>
  <div class="col-title" style="left:354px;top:968px;">Lorem Ipsum</div>
  <div class="col-title" style="left:571px;top:968px;">Lorem Ipsum</div>
  <div class="col-text" style="left:141px;top:1005px;">Excepteur sint occaecat cupidatat non proident, sunt in Excepteur sint occaecat cupidatat non Excepteur sint occaecat cupidatat non proident, sunt in culpa , sunt in culpa</div>
  <div class="col-text" style="left:359px;top:1007px;">Excepteur sint occaecat cupidatat non proident, sunt in Excepteur sint occaecat cupidatat non Excepteur sint occaecat cupidatat non proident, sunt in culpa , sunt in culpa</div>
  <div class="col-text" style="left:576px;top:1007px;">Excepteur sint occaecat cupidatat non proident, sunt in Excepteur sint occaecat cupidatat non Excepteur sint occaecat cupidatat non proident, sunt in culpa , sunt in culpa</div>
  <div class="pill-label" style="left:645px;top:1158px;width:114px;height:28px;background:var(--amber);border-radius:9px;font-size:14px;">mehr lesen</div>

  <footer class="site-footer" style="top:1266px;">
    <div class="foot-dark"></div><div class="foot-band"></div>
    <span class="foot-line" style="left:262px;"></span><span class="foot-line" style="left:620px;"></span>
    <div class="foot-title">Kontak Uns</div>
    <div class="field" style="left:291px;top:77px;width:93px;">Name</div>
    <div class="field" style="left:398px;top:77px;width:90px;">Email</div>
    <div class="field" style="left:499px;top:77px;width:94px;">Telefonnummer</div>
    <div class="field" style="left:291px;top:107px;width:197px;height:23px;">Nachricht</div>
    <div class="send">Schicken</div>
    <div class="info" style="top:83px;"><i></i>Location</div>
    <div class="info" style="top:97px;"><i></i>+49 5431 908765</div>
    <div class="info" style="top:111px;"><i></i>kontakt@brandtner-agrar.de</div>
    <div class="footer-brand"><span class="brand">Brandtner</span></div>
    <span class="social" style="left:408px;"></span><span class="social" style="left:426px;"></span><span class="social" style="left:444px;"></span><span class="social" style="left:462px;"></span>
    <div class="copyright">Copyright 2023 All Right Reserved</div>
  </footer>
</section>

<!-- ============ Firmenpräsentation ============ -->
<section class="page page-company" style="left:1328px;top:1077px;height:1253px;transform:scale(.6833);">
  <header class="site-header">
    <span class="brand-tab"></span>
    <div class="nav-bar">
      <span class="brand">Brandtner</span>
      <div class="nav"><span class="active">LANDWIRT</span><span>GESCHÄFTSPARTNER</span><span>LIEFERANTEN</span><span>PRODUKTE</span><span>FIRMENPRÄSENTATION</span></div>
      <svg class="search" viewBox="0 0 20 20"><circle cx="8" cy="8" r="6" fill="none" stroke="#fff" stroke-width="2"/><line x1="12.5" y1="12.5" x2="18" y2="18" stroke="#fff" stroke-width="2.5"/></svg>
    </div>
    <span class="nav-rule"></span>
  </header>
  <div class="photo ph-field" role="img" aria-label="Weites Ackerfeld im Abendlicht" style="left:0;top:101px;width:884px;height:225px;"></div>
  <div style="left:142px;top:135px;width:597px;height:145px;background:rgba(70,60,50,.62);border-radius:8px;"></div>
  <div style="left:152px;top:142px;width:577px;text-align:center;font-size:14.5px;line-height:17.5px;color:var(--white);">Excepteur sint occaecat cupidatat non proident, sunt in culpa qExcepteur sint occaecat cupidatat non proident, sunt in culpa qui officia deserunt mollit anim id esExcepteur sint occaecat cupidatat non proident, sunt in culpa qui officia deserunt mollit anim id esExcepteur sint occaecat cupidatat non proident, sunt in culpa qui officia deserunt mollit anim id esExcepteur sint occaecat cupidatat non proident, sunt in culpa qui officia deserunt mollit anim id es officia deserunt mollit anim id es</div>

  <svg style="left:152px;top:374px;width:580px;height:174px;" viewBox="0 0 580 174"><path d="M24,58 L556,0 Q580,0 580,24 L580,150 Q580,174 556,174 L24,174 Q0,174 0,150 L0,82 Q0,60 24,58 Z" fill="#f5c823"/></svg>
  <svg style="left:273px;top:362px;width:32px;height:32px;" viewBox="0 0 32 32"><path d="M16,2 L29,7 L29,16 Q29,26 16,31 Q3,26 3,16 L3,7 Z" fill="#1e1e1f"/><polyline points="10,16 14,20 22,12" fill="none" stroke="#fff" stroke-width="3"/></svg>
  <svg style="left:423px;top:358px;width:32px;height:38px;" viewBox="0 0 32 38"><circle cx="16" cy="13" r="12" fill="#1e1e1f"/><polygon points="9,22 6,37 16,31 26,37 23,22" fill="#1e1e1f"/><polyline points="10,13 14,17 22,9" fill="none" stroke="#fff" stroke-width="2.5"/></svg>
  <svg style="left:584px;top:362px;width:32px;height:32px;" viewBox="0 0 32 32"><circle cx="16" cy="16" r="15" fill="#1e1e1f"/><path d="M16,24 L8,16 Q5,11 10,9 Q14,8 16,12 Q18,8 22,9 Q27,11 24,16 Z" fill="#f5c823"/></svg>
  <div class="callout-text" style="left:240px;top:434px;width:96px;text-align:center;font-size:8px;line-height:10px;">Excepteur sint occaecat cupidatat non proident, sunt in culpa qui officia deserunt mollit anim id es Excepteur sint occaecat cupidatat non proident, sunt in culpa qui officia deserunt mollit anim id es</div>
  <div class="callout-text" style="left:392px;top:434px;width:96px;text-align:center;font-size:8px;line-height:10px;">Excepteur sint occaecat cupidatat non proident, sunt in culpa qui officia deserunt mollit anim id es Excepteur sint occaecat cupidatat non proident mollit anim id es</div>
  <div class="callout-text" style="left:548px;top:434px;width:100px;text-align:center;font-size:8px;line-height:10px;">Excepteur sint occaecat cupidatat non proident, sunt in culpa qui officia deserunt mollit anim id es Excepteur sint occaecat cupidatat non proident, sunt in culpa qui officia deserunt mollit anim id es</div>

  <svg style="left:0;top:830px;width:884px;height:150px;" viewBox="0 0 884 150"><polygon points="0,0 884,70 884,150 0,150" fill="#f5c823"/></svg>
  <div class="why" style="top:597px;">
    <svg style="left:0;top:0;width:884px;height:342px;" viewBox="0 0 884 342"><polygon points="0,0 884,0 884,342 0,222" fill="#262627"/></svg>
    <div class="why-title">Warum Uns Wählen?</div>
    <div class="why-sub">Excepteur sint occaecat cupidatat non proident, sunt in culpa qui officia deserunt mollit anim id es</div>
    <div class="why-item" style="left:211px;top:114px;"><span class="why-dot"></span><b>Lorem Ipsum</b><p>Excepteur sint occaecat cupidatat non proident, sunt in culpa</p></div>
    <div class="why-item" style="left:347px;top:114px;"><span class="why-dot"></span><b>Lorem Ipsum</b><p>Excepteur sint occaecat cupidatat non proident, sunt in culpa</p></div>
    <div class="why-item" style="left:211px;top:169px;"><span class="why-dot"></span><b>Lorem Ipsum</b><p>Excepteur sint occaecat cupidatat non proident, sunt in culpa</p></div>
    <div class="why-item" style="left:347px;top:169px;"><span class="why-dot"></span><b>Lorem Ipsum</b><p>Excepteur sint occaecat cupidatat non proident, sunt in culpa</p></div>
    <div class="pill" style="left:387px;top:235px;width:68px;height:17px;"></div>
    <div style="left:545px;top:39px;width:300px;height:205px;background:var(--yellow);border-radius:4px;"></div>
    <div class="photo ph-harvest" role="img" aria-label="Mähdrescher bei der Weizenernte" style="left:535px;top:49px;width:300px;height:205px;"></div>
  </div>

  <footer class="site-footer" style="top:978px;">
    <div class="foot-dark"></div><div class="foot-band"></div>
    <span class="foot-line" style="left:262px;"></span><span class="foot-line" style="left:620px;"></span>
    <div class="foot-title">Kontak Uns</div>
    <div class="field" style="left:291px;top:77px;width:93px;">Name</div>
    <div class="field" style="left:398px;top:77px;width:90px;">Email</div>
    <div class="field" style="left:499px;top:77px;width:94px;">Telefonnummer</div>
    <div class="field" style="left:291px;top:107px;width:197px;height:23px;">Nachricht</div>
    <div class="send">Schicken</div>
    <div class="info" style="top:83px;"><i></i>Location</div>
    <div class="info" style="top:97px;"><i></i>+49 5431 908765</div>
    <div class="info" style="top:111px;"><i></i>kontakt@brandtner-agrar.de</div>
    <div class="footer-brand"><span class="brand">Brandtner</span></div>
    <span class="social" style="left:408px;"></span><span class="social" style="left:426px;"></span><span class="social" style="left:444px;"></span><span class="social" style="left:462px;"></span>
    <div class="copyright">Copyright 2023 All Right Reserved</div>
  </footer>
</section>

</div>
</body>
</html>
```